Property Developer - Simple yet Sophisticated and Sharp Business Card

We are a medium sized property developer involved mainly in townhouse developments and land subdivisions.

The company is looking for a simple, sharp and sophisticated business card that will be given to contractors, land owners, financiers etc and thus will need to look professional.

Property development related graphics and art can be used, however the card is not to be too "busy" or crowded. Our company name is Kestrel Developments which could possibly be incorporated into the graphics or artwork.

Single sided and/or double sided designs will be acceptable.

A Simple, Sophisticated, Sharp design please!

Good Luck !

```html
<!DOCTYPE html>
<html lang="en">
<head>
<meta charset="utf-8">
<title>Kestrel Developments – Business Card</title>
<link rel="stylesheet" href="https://fonts.googleapis.com/css2?family=Jost:wght@700&display=swap">
<style>
  :root {
    --page: #ececea;
    --ink: #0a0a0a;
    --paper: #ffffff;
    --paper-shade: #f1f1f1;
  }
  * { margin: 0; padding: 0; box-sizing: border-box; }
  html, body { width: 1200px; height: 920px; overflow: hidden; }
  body {
    background: var(--page);
    position: relative;
    font-family: "Jost", "Futura", sans-serif;
    font-weight: 700;
  }
  .card {
    position: absolute;
    left: 262px;
    width: 675px;
    height: 374px;
  }
  .card-front {
    top: 66px;
    background: var(--paper);
    border: 2.5px solid var(--ink);
  }
  .card-back  { top: 470px; background: var(--ink); color: var(--paper); }
  .card svg { position: absolute; inset: 0; width: 100%; height: 100%; }

  .front-artwork {
    position: absolute;
    inset: 0;
    background: radial-gradient(ellipse at center, var(--paper) 40%, var(--paper-shade) 100%);
  }

  .wordmark-panel {
    position: absolute;
    left: 169px; top: 70px;
    width: 349px; height: 202px;
    background: var(--paper);
    border: 2.5px solid var(--ink);
    display: flex; flex-direction: column;
    align-items: center; justify-content: center;
    color: var(--ink);
    text-transform: uppercase;
  }
  .wordmark-main { font-size: 74px; line-height: 1; letter-spacing: -1px; margin-top: 14px; }
  .wordmark-sub  { font-size: 20px; line-height: 1; letter-spacing: 6px; margin-top: 8px; margin-right: -6px; }

  .contact-list {
    position: absolute;
    left: 93px; top: 256px;
    list-style: none;
    font-size: 15px;
    line-height: 20px;
    letter-spacing: 0.3px;
  }
</style>
</head>
<body>

<section class="card card-front">
  <div class="front-artwork" role="img" aria-label="Architectural perspective artwork framing the company name"></div>
  <div class="wordmark-panel">
    <span class="wordmark-main">Kestrel</span>
    <span class="wordmark-sub">Developments</span>
  </div>
</section>

<section class="card card-back">
  <svg viewBox="0 0 675 374" aria-hidden="true">
    <polyline points="75,0 75,342 673,342" fill="none" stroke="var(--paper)" stroke-width="2.5"/>
  </svg>
  <ul class="contact-list">
    <li>Phone: (07) 3000 4821</li>
    <li>Fax: (07) 3000 4822</li>
    <li>Email: projects.kestreldev@example.com</li>
    <li>Postal: PO Box 2870 Harbourview QLD 4000</li>
  </ul>
</section>

</body>
</html>
```